Full re-design of visual identity

We have just re-designed our logo and would like to apply it on our folders, business cards, stationery, and etc... we are attaching new logo + the material we need to re-design... we will provide full corel draw files to help make job easier and also because lot of icons and artwork can be still used...

any doubts we are at your disposal. thanks in advance.

```html
<!DOCTYPE html>
<html lang="pt-BR">
<head>
<meta charset="utf-8">
<title>Lumora – Stationery Set</title>
<link href="https://fonts.googleapis.com/css2?family=PT+Sans:wght@400;700&family=Roboto+Condensed:wght@400;700&display=swap" rel="stylesheet">
<style>
  :root{
    --backdrop:#80858b;
    --paper:#ffffff;
    --ink:#1d1d1d;
    --brand-grey:#6f6f6f;
    --orange:#f47b20;
    --orange-deep:#c9491f;
    --orange-mid:#e2641f;
    --label-red:#d2401f;
  }
  *{box-sizing:border-box;margin:0;padding:0}
  html,body{width:1200px;height:1071px;overflow:hidden}
  body{background:var(--backdrop);position:relative;font-family:"PT Sans",sans-serif;color:var(--ink)}

  .sheet{position:absolute;background:var(--paper);overflow:hidden}

  .brand{position:absolute;display:flex;align-items:center;gap:6px;
    font-family:"PT Sans",sans-serif;font-weight:700;color:var(--brand-grey);letter-spacing:-1px;line-height:1}
  .brand-dot{border-radius:50%;background:var(--orange);flex:none}

  .brand-art{position:absolute}
  .brand-art--fade{background:linear-gradient(90deg,var(--orange-deep),var(--orange))}

  .contact{position:absolute;font-family:"PT Sans",sans-serif;line-height:1.25;color:#333}
  .contact .company{font-weight:700;color:var(--ink)}
  .contact .gap{height:0.9em}
  .contact .label{color:var(--label-red)}

  /* Letterhead */
  .letterhead{left:83px;top:78px;width:498px;height:705px}
  .letterhead .brand{left:45px;top:52px;font-size:56px}
  .letterhead .brand-dot{width:26px;height:26px}
  .salutation{position:absolute;left:46px;top:185px;font-family:"Roboto Condensed",sans-serif;font-size:13px;font-weight:700}
  .letter-body{position:absolute;left:46px;top:217px;width:402px;font-size:12.3px;line-height:15px;text-align:justify;hyphens:auto}
  .signature{position:absolute;left:55px;top:468px;width:110px;height:55px;
    background:linear-gradient(90deg,rgba(30,110,170,.15),rgba(30,110,170,.05));border-radius:4px}
  .letterhead .contact{left:46px;top:584px;font-size:8.6px}
  .letterhead .brand-art{left:260px;top:518px;width:238px;height:187px;border-top-left-radius:120px}

  /* Business card front */
  .card-front{left:712px;top:114px;width:335px;height:205px}
  .card-front .edge{position:absolute;left:0;top:0;width:9px;height:100%;background:var(--orange)}
  .card-front .brand{left:22px;top:22px;font-size:38px}
  .card-front .brand-dot{width:18px;height:18px}
  .card-front .brand-art{left:160px;top:30px;width:175px;height:175px;border-top-left-radius:90px;
    background:linear-gradient(200deg,var(--orange),var(--orange-deep))}
  .role{position:absolute;right:9px;top:78px;text-align:right;color:#fff;line-height:1.1}
  .role .dept{font-weight:700;font-size:13.5px}
  .role .title{font-size:11.5px}
  .card-front .contact{left:21px;top:103px;font-size:8.8px}

  /* Business card back */
  .card-back{left:712px;top:397px;width:335px;height:204px;background:linear-gradient(90deg,#f26f14,#ff7a10)}
  .card-back .brand{left:40px;top:70px;font-size:64px;color:#fff}
  .card-back .brand-dot{width:30px;height:30px;background:#fff}

  /* DL envelope */
  .dl-envelope{left:285px;top:813px;width:408px;height:205px}
  .dl-envelope .brand-art{left:0;top:30px;width:200px;height:175px;border-top-right-radius:100px}
  .dl-envelope .brand{left:247px;top:24px;font-size:30px}
  .dl-envelope .brand-dot{width:14px;height:14px}
  .dl-envelope .contact{left:247px;top:131px;font-size:7.2px}

  /* Open envelope, laid flat */
  .open-envelope{left:724px;top:675px;width:407px;height:286px;background:transparent;overflow:visible}
  .open-envelope svg{position:absolute;left:0;top:0}
  .open-envelope .brand{left:221px;top:222px;font-size:32px}
  .open-envelope .brand-dot{width:15px;height:15px}
</style>
</head>
<body>

<section class="sheet letterhead" aria-label="Letterhead">
  <div class="brand">Lumora<span class="brand-dot"></span></div>
  <h1 class="salutation">Dear Someone&nbsp; Somebody</h1>
  <p class="letter-body">Lorem ipsum dolor sit amet, consectetur adipiscing elit. Donec orci purus, luctus vitae dignissim eu, iaculis sed purus. Vivamus faucibus, ipsum nec aliquet viverra, leo mauris condimentum ligula, sit amet sagittis enim ligula quis arcu. Nam egestas tortor id nisi porttitor mattis. In tortor ante, ultricies in suscipit aum nec aliquet viverra, leo mauris condimentum ligula, sit amet sagittis enim ligula quis arcu. Nam egestas tortor id nisi porttitor mattis. In tortor ante, ultricies in suscipit a, tempus non massa. Vivamus et auctor mi. Fusce vel massa nulla. Pha, tempus non massa. Vivamus et auctor mi. Fusce vel massa nulla. Phasellus nec eros mauris, et scelerisque orci. Donec malesuada orci vitae nulla accumsan porta a id massa. Quisque accumsan iaculis magna sit amet fringilla. Maecenas consequat, magna eget tincidunt semper, odio nibh rutrum mi, id feugiat ante nisi eu risus. Vestibulum nunc orci, rhoncus a placerat in, ultricies in mi. Cras mattis varius eros, vel fringilla nisi suscipit eget.</p>
  <div class="signature" role="img" aria-label="Handwritten signature"></div>
  <address class="contact">
    <div class="company">Lumora-Telecomunicações e internet</div>
    <div>Rua das Palmeiras,412 - jd.Aurora</div>
    <div>CEP 13400-120 - Vale Verde - SP</div>
    <div class="gap"></div>
    <div><span class="label">Tel.:</span> (11) 4020-5731</div>
    <div><span class="label">Email:</span> contato@lumora.com.br</div>
    <div><span class="label">Web:</span> www.lumora.com.br</div>
  </address>
  <div class="brand-art brand-art--fade" role="img" aria-label="Orange brand decoration"></div>
</section>

<section class="sheet card-front" aria-label="Business card front">
  <div class="edge"></div>
  <div class="brand">Lumora<span class="brand-dot"></span></div>
  <div class="brand-art" role="img" aria-label="Orange brand decoration"></div>
  <div class="role"><div class="dept">Atendimento</div><div class="title">Manager</div></div>
  <address class="contact">
    <div class="company">Lumora-Telecomunicações e internet</div>
    <div>Rua das Palmeiras,412 - jd.Aurora</div>
    <div>CEP 13400-120 - Vale Verde - SP</div>
    <div class="gap"></div>
    <div><span class="label">Tel.:</span> (11) 4020-5731</div>
    <div><span class="label">Email:</span> contato@lumora.com.br</div>
    <div><span class="label">Web:</span> www.lumora.com.br</div>
  </address>
</section>

<section class="sheet card-back" aria-label="Business card back">
  <div class="brand">Lumora<span class="brand-dot"></span></div>
</section>

<section class="sheet dl-envelope" aria-label="DL envelope">
  <div class="brand-art brand-art--fade" role="img" aria-label="Orange brand decoration"></div>
  <div class="brand">Lumora<span class="brand-dot"></span></div>
  <address class="contact">
    <div class="company">Lumora-Telecomunicações e internet</div>
    <div>Rua das Palmeiras,412 - jd.Aurora</div>
    <div>CEP 13400-120 - Vale Verde - SP</div>
    <div class="gap"></div>
    <div><span class="label">Tel.:</span> (11) 4020-5731</div>
    <div><span class="label">Email:</span> contato@lumora.com.br</div>
    <div><span class="label">Web:</span> www.lumora.com.br</div>
  </address>
</section>

<section class="sheet open-envelope" aria-label="Envelope">
  <svg width="407" height="286" viewBox="0 0 407 286" aria-hidden="true">
    <defs>
      <linearGradient id="flap" x1="0" y1="0" x2="0" y2="1">
        <stop offset="0" stop-color="#f27a1c"/>
        <stop offset="1" stop-color="#d9531c"/>
      </linearGradient>
    </defs>
    <path d="M0 105 L0 10 Q0 0 12 0 L395 0 Q407 0 407 10 L407 105 Z" fill="url(#flap)"/>
    <rect x="0" y="95" width="407" height="191" fill="#e1621f"/>
    <path d="M0 105 L30 105 L30 140 L0 286 Z" fill="#ffffff"/>
    <path d="M407 105 L377 105 L377 140 L407 286 Z" fill="#ffffff"/>
    <path d="M28 140 L30 145 L377 145 L379 140 Z" fill="#ffffff"/>
    <rect x="0" y="140" width="407" height="146" fill="#ffffff"/>
  </svg>
  <div class="brand">Lumora<span class="brand-dot"></span></div>
</section>

</body>
</html>
```